Car transport business

We need a new business card design. Attached is our old card sample. I would just like to adjust the logo colors (blue and red) to be brighter. I changed my name to the brighter red and the word dispatcher to a brighter blue as an example. But you can adjust those colors further. And then perhaps you can use the same colors for the card design but use your imagination.

As a suggestion so the card stands out I would like to add a clip art of car carrier truck. Attached are examples of that as well

```html
<!DOCTYPE html>
<html lang="en">
<head>
<meta charset="utf-8">
<title>Summit Haul – Business Card</title>
<link rel="stylesheet" href="https://fonts.googleapis.com/css2?family=Montserrat:wght@400;500;600;700&display=swap">
<style>
  :root {
    --page-bg: #dcdcdc;
    --card-white: #ffffff;
    --brand-red: #c11f2f;
    --brand-blue: #175a87;
    --back-blue: #165a86;
    --back-mark: #3a9be0;
  }
  * { box-sizing: border-box; margin: 0; padding: 0; }
  html, body {
    width: 1200px; height: 1200px; overflow: hidden;
    background: var(--page-bg);
    font-family: "Montserrat", Arial, sans-serif;
  }
  .card {
    position: absolute;
    left: 207px;
    width: 786px;
    height: 449px;
    overflow: hidden;
  }
  .card-front { top: 112px; background: var(--card-white); }
  .card-back { top: 640px; background: var(--back-blue); }

  .brand {
    position: absolute;
    display: flex;
    align-items: center;
    gap: 12px;
    font-weight: 700;
    letter-spacing: 1px;
    text-transform: uppercase;
  }
  .brand-dot { border-radius: 50%; flex: none; }
  .card-front .brand { left: 49px; top: 78px; font-size: 30px; color: var(--brand-blue); }
  .card-front .brand-dot { width: 26px; height: 26px; background: var(--brand-red); }
  .card-back .brand {
    left: 0; right: 0; top: 196px; justify-content: center;
    font-size: 52px; color: var(--back-mark);
  }
  .card-back .brand-dot { width: 44px; height: 44px; background: var(--back-mark); }

  .person {
    position: absolute;
    right: 51px;
    top: 188px;
    text-align: right;
  }
  .person-name {
    font-size: 43px; font-weight: 600; color: var(--brand-red);
    line-height: 1; letter-spacing: 0.5px;
  }
  .person-role {
    margin-top: 6px;
    font-size: 19px; font-weight: 500; color: var(--brand-blue);
    letter-spacing: 0.5px;
  }
  .divider {
    position: absolute; left: 49px; top: 240px;
    width: 540px; height: 1.5px; background: var(--brand-red);
  }
  .edge-bar {
    position: absolute; left: 767px; top: 195px;
    width: 19px; height: 52px; background: var(--brand-blue);
  }

  .contacts {
    position: absolute; left: 49px; top: 333px;
    list-style: none;
  }
  .contacts li {
    display: flex; align-items: center; gap: 7px;
    height: 25.5px;
    font-size: 19px; color: var(--brand-blue);
  }
  .contacts svg { width: 16px; height: 16px; flex: none; fill: none; stroke: var(--brand-red); stroke-width: 2; }
  .contacts svg .solid { fill: var(--brand-red); stroke: none; }
</style>
</head>
<body>
  <section class="card card-front">
    <div class="brand"><span class="brand-dot"></span>Summit Haul</div>

    <div class="person">
      <div class="person-name">OMAR REYES</div>
      <div class="person-role">DISPATCHER</div>
    </div>
    <div class="divider"></div>
    <div class="edge-bar"></div>

    <ul class="contacts">
      <li>
        <svg viewBox="0 0 16 16" aria-hidden="true"><path d="M4 1.5 L6.5 4.5 L5 6.5 Q6.5 10 9.5 11 L11.5 9.5 L14.5 12 L12.5 14.5 Q5 13.5 1.5 3.5 Z"/></svg>
        555-318-2046
      </li>
      <li>
        <svg viewBox="0 0 16 16" aria-hidden="true"><rect class="solid" x="4" y="1" width="8" height="4"/><rect class="solid" x="1" y="5" width="14" height="7" rx="1"/><rect x="4.5" y="10" width="7" height="5" fill="#fff"/></svg>
        555-318-2071
      </li>
      <li>
        <svg viewBox="0 0 16 16" aria-hidden="true"><rect x="1.5" y="3.5" width="13" height="9"/><path d="M1.5 3.5 L8 9 L14.5 3.5"/></svg>
        summithaulinc@example.com
      </li>
    </ul>
  </section>

  <section class="card card-back">
    <div class="brand"><span class="brand-dot"></span>Summit Haul</div>
  </section>
</body>
</html>
```